Brightway Haus Inc. Business Card Design

Brightway Haus Inc. is in search of a great clean design for our business cards!

Looking to incorporate our full logo and watermark on side one (however, I am open to having the text and watermark separated within the design.)

On side two, I am looking to have contact information (Name, Position, Phone #, Email, Website (www.thebrightwayhaus.ca). Can have the logo and/or watermark as part of the design if applicable.

Please add tagline "Where Shine Counts" on either side 1 or 2. This tagline can be in a sans serif, serif or cursive font as long as it compliments overall design. Capitalization can be title or sentence case depending on how it fits within the design.

Get creative!! Looking for a clean, crisp, premium design! Looking for a glossy card finish with spot UV features when printed. Cards will also be printed with rounded corners. Standard dimensions (3.5 x 2).

Target Market(s)

B2B - primary clients are business owners or property management corporations. (residential jobs are few and far between)

Industry/Entity Type

Business

Contact Information for Business Card

- clean, crisp design
- double sided
- spot UV accents and glossy finish upon printing
- standard business card size (3.5 x 2) with rounded corners
- please see project description for requirements per side

Font styles to use
Sans Serif

Requirements
Must have
• - adequate bleeds with print ready files
• - cohesive design elements between side 1 & 2
• - spot UV elements (can be on both sides or just one, use your discretion)
• - colour pallet should match the logo file provided
• - incorporate tagline "where shine counts" (this tagline can be in a serif or sans serif font as long as it is complimentary to the overall design.
Nice to have
• - Premium elements with a clean design
Should not have
• - Please omit cartoon or whimsical like designs, think premium.
• - Colours should not stray from the pallet of the provided logo.

```html
<!DOCTYPE html>
<html lang="en">
<head>
<meta charset="utf-8">
<title>Brightway Haus Inc. Business Card</title>
<link href="https://fonts.googleapis.com/css2?family=Open+Sans:wght@400;600;700&display=swap" rel="stylesheet">
<style>
  :root {
    --backdrop: #2b2b2b;
    --paper: #ffffff;
    --teal: #10b8b8;
    --navy: #1b2452;
    --silver: #c9cbd0;
    --white: #ffffff;
  }
  * { margin: 0; padding: 0; box-sizing: border-box; }
  html, body {
    width: 1200px; height: 960px; overflow: hidden;
    background: var(--backdrop);
    font-family: "Open Sans", sans-serif;
  }
  .card {
    position: absolute;
    width: 600px; height: 343px;
    border-radius: 22px;
    overflow: hidden;
  }
  .card-front { left: 314px; top: 113px; background: var(--paper); }
  .card-back { left: 311px; top: 472px; background: var(--navy); }
  .swoosh { position: absolute; inset: 0; }
  .wordmark {
    position: absolute;
    display: flex; align-items: center; gap: 8px;
    font-weight: 700; white-space: nowrap; letter-spacing: -0.5px;
  }
  .wordmark-front { left: 46px; top: 82px; color: var(--navy); font-size: 29px; }
  .wordmark-front .mark { width: 26px; height: 26px; background: var(--teal); }
  .wordmark-back {
    left: 0; right: 0; top: 142px; justify-content: center;
    color: var(--silver); font-size: 42px;
  }
  .contact {
    position: absolute; right: 26px; top: 136px;
    color: var(--white); text-align: right; font-size: 14.5px; line-height: 19.5px;
  }
  .contact .name { font-weight: 700; font-size: 16px; }
  .contact .role { font-size: 16px; margin-bottom: 8px; }
  .contact .address { margin-bottom: 5px; }
  .contact .line { display: flex; justify-content: flex-end; align-items: center; gap: 8px; }
  .contact .line svg { width: 12px; height: 12px; fill: var(--white); }
  .tagline {
    position: absolute; left: 100px; right: 85px; top: 276px;
    display: flex; align-items: center; gap: 2px;
    color: var(--white); font-weight: 600; font-size: 17px; white-space: nowrap;
  }
  .tagline .rule { flex: 1; height: 1px; }
  .tagline .rule-left { background: linear-gradient(to right, transparent, var(--white)); }
  .tagline .rule-right { background: linear-gradient(to left, transparent, var(--white)); }
</style>
</head>
<body>
  <section class="card card-front">
    <svg class="swoosh" viewBox="0 0 600 343" aria-hidden="true">
      <path d="M428 0 L472 0 C492 120 330 262 126 343 C300 250 462 120 428 0 Z" fill="var(--navy)"/>
      <path d="M478 0 C494 122 340 258 126 343 L600 343 L600 0 Z" fill="var(--paper)"/>
      <path d="M482 0 C498 124 346 260 130 343 L600 343 L600 0 Z" fill="var(--teal)"/>
    </svg>
    <div class="wordmark wordmark-front"><span class="mark"></span>BRIGHTWAY HAUS INC.</div>
    <div class="contact">
      <div class="name">MAREN HOLT</div>
      <div class="role">CEO/FOUNDER</div>
      <div class="address">4120 Larkspur Court<br>Kelowna, BC V1Y 2K8</div>
      <div class="line">250 418 6273
        <svg viewBox="0 0 12 12"><path d="M1 4 Q6 0 11 4 L9 5 L8 3.5 Q6 3 4 3.5 L3 5 Z M3 6 H9 L10 11 H2 Z"/></svg></div>
      <div class="line">250 762 3190
        <svg viewBox="0 0 12 12"><path d="M3 0.5 H9 V11.5 H3 Z M4 2 V9.5 H8 V2 Z" fill-rule="evenodd"/></svg></div>
      <div class="line">250 417 5582
        <svg viewBox="0 0 12 12"><path d="M3 1 H9 V4 H3 Z M1 5 H11 V9 H9 V11 H3 V9 H1 Z"/></svg></div>
      <div class="line">maren@brightway.ca
        <svg viewBox="0 0 12 12"><path d="M1 3 H11 V9.5 H1 Z"/><path d="M1 3 L6 7 L11 3" fill="none" stroke="var(--teal)" stroke-width="1"/></svg></div>
      <div class="line">www.thebrightwayhaus.ca
        <svg viewBox="0 0 12 12"><circle cx="6" cy="6" r="5.5"/></svg></div>
    </div>
  </section>

  <section class="card card-back">
    <div class="wordmark wordmark-back">BRIGHTWAY HAUS INC.</div>
    <div class="tagline">
      <span class="rule rule-left"></span>Where Shine Counts<span class="rule rule-right"></span>
    </div>
  </section>
</body>
</html>
```